Automotive Accessories Business Card

Design a business template that match our new logo design and our industry.

https://www.qelmotorgear.com/

Target Market(s)

Aftermarket auto parts and accessories

Industry/Entity Type

automotive

Contact Information for Business Card

company logo

Font styles to use
Serif
Sans Serif

Colors
EB3D1F
EC4F4E
F09395
F8D3D4
FCEDEE

```html
<!DOCTYPE html>
<html lang="en">
<head>
<meta charset="utf-8">
<title>QEL Motor Gear – Business Card</title>
<link rel="stylesheet" href="https://fonts.googleapis.com/css2?family=Open+Sans:wght@400;600;700&family=Roboto:wght@700;900&display=swap">
<style>
  :root {
    --red: #e0262f;
    --red-soft: #f8d3d4;
    --red-faint: #fcedee;
    --ink: #3a3a3c;
    --ink-soft: #5a5a5c;
    --grey-block: #d9d9d9;
    --card-white: #f6f6f6;
    --carbon-dark: #2a2a2b;
    --carbon-mid: #5a5a5c;
    --stage: #e9e6e2;
  }
  * { box-sizing: border-box; margin: 0; padding: 0; }
  html, body { width: 1200px; height: 960px; overflow: hidden; }
  body {
    background: var(--stage);
    font-family: "Open Sans", sans-serif;
    display: flex;
    flex-direction: column;
    align-items: center;
    justify-content: center;
    gap: 30px;
  }
  .card {
    width: 760px;
    height: 434px;
    position: relative;
    border-radius: 4px;
    box-shadow: 0 8px 24px rgba(0,0,0,.18);
    overflow: hidden;
  }
  /* Front */
  .card-front { background: linear-gradient(160deg, #ffffff 0%, var(--card-white) 60%, #ececec 100%); }
  .front-accent {
    position: absolute;
    left: 0; bottom: 0;
    width: 300px; height: 150px;
    background:
      linear-gradient(180deg, rgba(246,246,246,1) 0%, rgba(246,246,246,0) 40%),
      linear-gradient(90deg, rgba(217,217,217,.55) 0%, rgba(248,211,212,.6) 55%, rgba(252,237,238,.35) 100%);
  }
  .brand {
    position: absolute;
    top: 70px; left: 290px;
    display: flex; align-items: center; gap: 12px;
  }
  .brand-mark { width: 26px; height: 26px; background: var(--red); }
  .brand-name {
    font-family: "Roboto", sans-serif;
    font-weight: 900;
    font-size: 36px;
    letter-spacing: 1px;
    color: var(--ink);
    text-transform: uppercase;
  }
  .contact {
    position: absolute;
    top: 172px; right: 470px;
    list-style: none;
    font-size: 15px;
    color: var(--ink);
    line-height: 28px;
  }
  .contact li { display: flex; align-items: center; justify-content: flex-end; gap: 10px; }
  .contact svg { width: 16px; height: 16px; flex: none; }
  .contact .web-key { color: var(--red); font-weight: 700; }
  .divider {
    position: absolute;
    top: 190px; left: 322px;
    width: 3px; height: 92px;
    background: var(--red);
  }
  .person { position: absolute; top: 204px; left: 352px; }
  .person-name {
    font-family: "Roboto", sans-serif;
    font-weight: 900;
    font-size: 34px;
    letter-spacing: 1px;
    color: var(--ink);
    text-transform: uppercase;
    line-height: 1.1;
  }
  .person-role { font-size: 18px; color: var(--ink-soft); margin-top: 2px; }
  /* Back */
  .card-back { background: var(--carbon-dark); }
  .back-pattern {
    position: absolute; inset: 0;
    background:
      radial-gradient(ellipse at 15% 5%, rgba(200,200,200,.35) 0%, rgba(200,200,200,0) 45%),
      linear-gradient(135deg, var(--carbon-mid) 0%, #3e3e40 45%, var(--carbon-dark) 100%);
  }
  .back-accent {
    position: absolute;
    left: 70px; top: 150px;
    width: 170px; height: 80px;
    background: linear-gradient(160deg, #ffffff 0%, #f0a9ab 45%, var(--red) 100%);
  }
</style>
</head>
<body>
  <section class="card card-front" aria-label="Business card front">
    <div class="front-accent" role="img" aria-label="Faint grey and pink checkered flag decoration"></div>

    <div class="brand">
      <span class="brand-mark"></span>
      <span class="brand-name">QEL Motor Gear</span>
    </div>

    <ul class="contact">
      <li>1-866-555-0142
        <svg viewBox="0 0 24 24" aria-hidden="true"><path fill="#e0262f" d="M6.6 10.8a15.2 15.2 0 0 0 6.6 6.6l2.2-2.2a1 1 0 0 1 1-.25 11.4 11.4 0 0 0 3.6.57 1 1 0 0 1 1 1V20a1 1 0 0 1-1 1A17 17 0 0 1 3 4a1 1 0 0 1 1-1h3.5a1 1 0 0 1 1 1c0 1.25.2 2.45.57 3.57a1 1 0 0 1-.25 1z"/></svg>
      </li>
      <li>sales@qelmotorgear.com
        <svg viewBox="0 0 24 24" aria-hidden="true"><path d="M2 5h20v14H2z M2 5l10 8 10-8" fill="none" stroke="#e0262f" stroke-width="2"/></svg>
      </li>
      <li><span>www.<span class="web-key">qelmotorgear</span>.com</span>
        <svg viewBox="0 0 24 24" aria-hidden="true"><circle cx="12" cy="12" r="10" fill="none" stroke="#e0262f" stroke-width="2"/><path d="M2 12h20M12 2c3 3 3 17 0 20M12 2c-3 3-3 17 0 20" fill="none" stroke="#e0262f" stroke-width="1.6"/></svg>
      </li>
    </ul>

    <div class="divider"></div>

    <div class="person">
      <p class="person-name">Dana Whitlow</p>
      <p class="person-role">Sales Manager</p>
    </div>
  </section>

  <section class="card card-back" aria-label="Business card back">
    <div class="back-pattern" role="img" aria-label="Dark carbon checkered flag pattern filling the card"></div>
    <div class="back-accent" role="img" aria-label="Red and white checkered flag accent"></div>
  </section>
</body>
</html>
```